business card deign

Logo needs the following on it.
1. attached logo
2. Tagline - "From icy drinks to late-night tunes...we bring the fun!"
3. Name- Dalton Pikes, Founder and CPO
4. Address - 412 E. Carver Avenue, Ste 2207, Corwin Falls, KR. 33917
5. Phone - 555.318.4726

```html
<!DOCTYPE html>
<html lang="en">
<head>
<meta charset="utf-8">
<title>Bramble Business Card</title>
<link href="https://fonts.googleapis.com/css2?family=Montserrat:wght@400;500;700&display=swap" rel="stylesheet">
<style>
  :root {
    --ink: #111111;
    --card-dark: #1c1c1c;
    --paper: #ffffff;
    --muted: #4a4a4a;
    --stage: #d9d9d9;
  }
  * { box-sizing: border-box; margin: 0; padding: 0; }
  html, body { width: 1200px; height: 875px; overflow: hidden; }
  body {
    background: var(--stage);
    font-family: 'Montserrat', sans-serif;
    position: relative;
  }
  .card {
    position: absolute;
    left: 290px;
    width: 620px;
    height: 354px;
    border-radius: 22px;
    overflow: hidden;
  }
  .card-back { top: 60px; background: var(--card-dark); }
  .card-front { top: 461px; background: var(--paper); color: var(--ink); }

  .wordmark {
    font-family: 'Montserrat', sans-serif;
    font-weight: 700;
    letter-spacing: 0.45em;
    text-transform: uppercase;
    white-space: nowrap;
  }
  .card-back .wordmark {
    position: absolute;
    left: 0; right: 0; top: 50%;
    transform: translateY(-50%);
    text-align: center;
    color: var(--paper);
    font-size: 40px;
    padding-left: 0.45em;
  }
  .card-front .wordmark {
    position: absolute;
    right: 30px; top: 120px;
    font-size: 24px;
    color: var(--ink);
  }
  .divider {
    position: absolute;
    left: 40px; right: 30px; top: 186px;
    height: 2px;
    background: var(--ink);
  }
  .person { position: absolute; left: 40px; top: 132px; }
  .person-name { font-weight: 700; font-size: 22px; line-height: 1; }
  .person-title { font-size: 13px; color: var(--muted); margin-top: 5px; }

  .contacts { position: absolute; left: 40px; top: 204px; list-style: none; }
  .contacts li {
    display: flex; align-items: center; gap: 10px;
    font-size: 13px; height: 24px; color: var(--ink);
  }
  .contacts svg { width: 12px; height: 12px; fill: var(--ink); }

  .address {
    position: absolute; right: 30px; top: 200px;
    text-align: right; font-size: 12px; line-height: 1.45; color: var(--ink);
  }
  .tagline-band { position: absolute; left: 0; top: 286px; width: 620px; height: 36px; }
  .tagline {
    position: absolute; left: 40px; top: 294px;
    font-size: 13px; color: var(--paper); letter-spacing: 0.01em;
    white-space: nowrap;
  }
</style>
</head>
<body>
  <section class="card card-back" aria-label="Card back">
    <div class="wordmark">Bramble</div>
  </section>

  <section class="card card-front" aria-label="Card front">
    <div class="wordmark">Bramble</div>

    <div class="person">
      <div class="person-name">Dalton Pikes</div>
      <div class="person-title">Founder and CPO</div>
    </div>

    <div class="divider"></div>

    <ul class="contacts">
      <li>
        <svg viewBox="0 0 12 12" aria-hidden="true"><path d="M2.5 0.8l1.8 2.2-1 1.2c.7 1.6 2 2.9 3.6 3.6l1.2-1 2.2 1.8-.9 2C5.2 10.4 1.6 6.8 .6 1.7z"/></svg>
        555.318.4726
      </li>
      <li>
        <svg viewBox="0 0 12 12" aria-hidden="true"><path d="M0 2.5h12v7H0z M0.6 3l5.4 3.6L11.4 3" stroke="#fff" stroke-width="0.8"/></svg>
        info@brambleco.com
      </li>
      <li>
        <svg viewBox="0 0 12 12" aria-hidden="true"><circle cx="6" cy="6" r="5.6"/><path d="M0.6 6h10.8M6 .4c-2 2.8-2 8.4 0 11.2M6 .4c2 2.8 2 8.4 0 11.2" stroke="#fff" stroke-width="0.7" fill="none"/></svg>
        www.brambleco.com
      </li>
    </ul>

    <div class="address">412 E. Carver Avenue, Ste 2207,<br>Corwin Falls, KR. 33917</div>

    <svg class="tagline-band" viewBox="0 0 620 36" aria-hidden="true">
      <polygon points="0,0 548,0 536,36 0,36" fill="var(--ink)"/>
      <polygon points="556,0 620,0 620,36 544,36" fill="var(--muted)"/>
    </svg>
    <div class="tagline">From icy drinks to late-night tunes...we bring the fun</div>
  </section>
</body>
</html>
```